Corporate Business Card

Very professional, Modern, Not to busy, include phone address email, website
(253) 617-4930, 18761 52nd Avenue S, Kent, WA 98047, martin@plumlinegroup.com, varkoworks.com

Target Market(s)

Manufacturing

Industry/Entity Type

Aero, machining, manufacturing, Off road racing

Contact Information for Business Card

Phone, address email, website

```html
<!DOCTYPE html>
<html lang="en">
<head>
<meta charset="utf-8">
<title>Varko Works – Business Card</title>
<link rel="stylesheet" href="https://fonts.googleapis.com/css2?family=Zilla+Slab:wght@400;600&display=swap">
<style>
  :root {
    --card-bg: #ffffff;
    --brand-navy: #2e4472;
    --ink: #333333;
  }
  * { margin: 0; padding: 0; box-sizing: border-box; }
  html, body {
    width: 1200px;
    height: 682px;
    overflow: hidden;
    background: var(--card-bg);
  }
  .card {
    position: relative;
    width: 1200px;
    height: 682px;
    background: var(--card-bg);
    font-family: "Zilla Slab", Georgia, serif;
    color: var(--ink);
  }
  .brand-name {
    position: absolute;
    left: 558px;
    top: 150px;
    width: 490px;
    font-weight: 600;
    font-size: 74px;
    line-height: 1;
    letter-spacing: 1px;
    color: var(--brand-navy);
    white-space: nowrap;
  }
  .contact-list {
    position: absolute;
    left: 548px;
    top: 348px;
    list-style: none;
  }
  .contact-item {
    display: flex;
    align-items: flex-start;
    font-size: 37px;
    line-height: 42px;
    margin-bottom: 0;
  }
  .contact-icon {
    flex: 0 0 auto;
    width: 24px;
    height: 24px;
    margin: 9px 34px 0 4px;
    fill: var(--ink);
  }
  .contact-text { white-space: nowrap; }
</style>
</head>
<body>
  <main class="card">
    <h1 class="brand-name">Varko Works</h1>

    <ul class="contact-list">
      <li class="contact-item">
        <svg class="contact-icon" viewBox="0 0 24 24" aria-hidden="true">
          <rect x="5" y="1" width="14" height="22" rx="2.5"/>
          <rect x="7" y="4" width="10" height="14" fill="#fff"/>
          <circle cx="12" cy="20.5" r="1" fill="#fff"/>
        </svg>
        <span class="contact-text">(253) 617-4930</span>
      </li>
      <li class="contact-item">
        <svg class="contact-icon" viewBox="0 0 24 24" aria-hidden="true">
          <path d="M12 1a8 8 0 0 0-8 8c0 6 8 14 8 14s8-8 8-14a8 8 0 0 0-8-8zm0 11a3 3 0 1 1 0-6 3 3 0 0 1 0 6z"/>
        </svg>
        <span class="contact-text">18761 52nd Avenue S,<br>Kent, WA 98047</span>
      </li>
      <li class="contact-item">
        <svg class="contact-icon" viewBox="0 0 24 24" aria-hidden="true">
          <path d="M2 5h20v14H2z"/>
          <path d="M3 6l9 7 9-7" fill="none" stroke="#fff" stroke-width="1.8"/>
        </svg>
        <span class="contact-text">martin@plumlinegroup.com</span>
      </li>
      <li class="contact-item">
        <svg class="contact-icon" viewBox="0 0 24 24" aria-hidden="true">
          <circle cx="12" cy="12" r="10"/>
          <g fill="none" stroke="#fff" stroke-width="1.6">
            <ellipse cx="12" cy="12" rx="4" ry="10"/>
            <path d="M2 12h20M12 2v20"/>
          </g>
        </svg>
        <span class="contact-text">varkoworks.com</span>
      </li>
    </ul>
  </main>
</body>
</html>
```